Harborline Renewal Business Card Design

Professional and clean design. The design colors should flow with the logo. Two-sided card with the website on the back which is:

www.HarborlineRenewal.example.

"Specializing in Water Damage Restoration"

On the front I need the name, email, phone, and logo.

Name: Darnell Quisby
Email: Darnell@HarborlineRenewal.example
Phone: 555-318-2046 for now

I only have the Preview and Thumbnail right now but should have the source files uploaded within a day or two.

Target Market(s)

Flood victims, home owners with water damage from busted pipes etc...

Industry/Entity Type

Business

Contact Information for Business Card

Name: Darnell Quisby

Font styles to use
Serif
Sans Serif

Requirements
Must have
• Business Card Details Info

```html
<!DOCTYPE html>
<html lang="en">
<head>
<meta charset="utf-8">
<title>Harborline Renewal – Business Card</title>
<link rel="stylesheet" href="https://fonts.googleapis.com/css2?family=Cinzel:wght@600&family=Open+Sans:wght@400;600&display=swap">
<style>
  :root {
    --brand-blue: #2f9ad6;
    --brand-blue-deep: #1f86c4;
    --brand-blue-light: #5fb8e8;
    --ink: #3c3c3c;
    --wave-grey: #b9bcc0;
    --card-white: #ffffff;
    --backdrop: #e9ecef;
  }
  html, body {
    margin: 0;
    width: 1200px;
    height: 843px;
    overflow: hidden;
    background: var(--backdrop);
  }
  .canvas {
    position: relative;
    width: 1200px;
    height: 843px;
    display: flex;
    align-items: center;
    justify-content: center;
    gap: 50px;
  }
  .card {
    position: relative;
    width: 525px;
    height: 300px;
    border-radius: 18px;
    overflow: hidden;
    box-shadow: 0 6px 18px rgba(0,0,0,0.18);
  }

  /* Back side */
  .card-back {
    background: linear-gradient(160deg, var(--brand-blue-light), var(--brand-blue) 55%, var(--brand-blue-deep));
    color: var(--card-white);
    display: flex;
    flex-direction: column;
    align-items: center;
    justify-content: center;
    text-align: center;
  }
  .back-emblem {
    width: 92px;
    height: 92px;
    border-radius: 50%;
    background: var(--card-white);
    margin-bottom: 16px;
  }
  .back-name {
    font-family: "Cinzel", serif;
    font-weight: 600;
    font-size: 30px;
    letter-spacing: 1px;
    margin: 0 0 14px;
  }
  .back-tagline {
    font-family: "Open Sans", sans-serif;
    font-weight: 600;
    font-size: 16px;
    margin: 0 0 6px;
  }
  .back-web {
    font-family: "Open Sans", sans-serif;
    font-size: 14px;
    margin: 0;
  }

  /* Front side */
  .card-front {
    background: var(--card-white);
  }
  .front-brand {
    position: absolute;
    left: 28px;
    top: 52px;
    width: 190px;
    text-align: center;
  }
  .brand-dot {
    width: 58px;
    height: 58px;
    border-radius: 50%;
    background: var(--brand-blue);
    margin: 0 auto 10px;
  }
  .brand-name {
    font-family: "Cinzel", serif;
    font-weight: 600;
    font-size: 24px;
    line-height: 1.15;
    letter-spacing: 1px;
    color: var(--brand-blue);
    margin: 0;
  }
  .front-contact {
    position: absolute;
    left: 238px;
    top: 78px;
    font-family: "Open Sans", sans-serif;
  }
  .contact-name {
    font-weight: 600;
    font-size: 21px;
    color: var(--brand-blue);
    margin: 0 0 8px;
  }
  .contact-list {
    list-style: none;
    margin: 0;
    padding: 0;
    font-size: 13.5px;
    color: var(--ink);
  }
  .contact-list li {
    display: flex;
    align-items: center;
    gap: 8px;
    line-height: 22px;
  }
  .contact-icon {
    width: 13px;
    height: 13px;
    flex: none;
    fill: var(--brand-blue);
  }
  .front-wave {
    position: absolute;
    left: 0;
    bottom: 0;
    width: 525px;
    height: 110px;
  }
</style>
</head>
<body>
<main class="canvas">

  <section class="card card-back" aria-label="Card back">
    <div class="back-emblem"></div>
    <p class="back-name">Harborline Renewal</p>
    <p class="back-tagline">Specializing in Water Damage Restoration</p>
    <p class="back-web">www.HarborlineRenewal.example</p>
  </section>

  <section class="card card-front" aria-label="Card front">
    <div class="front-brand">
      <div class="brand-dot"></div>
      <p class="brand-name">Harborline<br>Renewal</p>
    </div>

    <div class="front-contact">
      <p class="contact-name">Darnell Quisby</p>
      <ul class="contact-list">
        <li>
          <svg class="contact-icon" viewBox="0 0 16 16" aria-hidden="true"><path d="M3.5 1 6 3.8 4.7 5.6c.8 1.9 2.3 3.4 4.2 4.3L10.6 8.6 14 11l-1.2 2.8C12.3 15 11 15 9.5 14.4 5.6 12.8 3 10 1.6 6.3 1 4.7 1.2 3.5 2.3 2.2z"/></svg>
          555-318-2046 for now
        </li>
        <li>
          <svg class="contact-icon" viewBox="0 0 16 16" aria-hidden="true"><path d="M1 3h14v1.2L8 8.6 1 4.2zM1 5.6l7 4.4 7-4.4V13H1z"/></svg>
          Darnell@HarborlineRenewal.example
        </li>
        <li>
          <svg class="contact-icon" viewBox="0 0 16 16" aria-hidden="true"><circle cx="8" cy="8" r="7"/></svg>
          www.HarborlineRenewal.example
        </li>
      </ul>
    </div>

    <svg class="front-wave" viewBox="0 0 525 110" preserveAspectRatio="none" aria-hidden="true">
      <path d="M0 28 C120 10 230 40 330 72 C410 96 470 100 525 92 L525 110 L0 110 Z" fill="var(--wave-grey)"/>
      <path d="M0 38 C120 22 230 52 330 82 C410 104 470 106 525 100 L525 110 L0 110 Z" fill="var(--card-white)"/>
      <path d="M0 46 C120 32 230 62 330 90 C410 108 470 110 525 104 L525 110 L0 110 Z" fill="var(--brand-blue)"/>
    </svg>
  </section>

</main>
</body>
</html>
```